Business Card Design Project

Business card based on attached logo

Todd Merrick
Todd@lorvantest.com
877-514-9073 ext. 318
Www.LorvanTest.com

Industry/Entity Type

Business

```html
<!DOCTYPE html>
<html lang="en">
<head>
<meta charset="utf-8">
<title>LorvanTest Business Cards</title>
<link rel="stylesheet" href="https://fonts.googleapis.com/css2?family=Archivo:wght@400;700;900&family=Questrial&display=swap">
<style>
  :root {
    --backdrop: #9a6a45;
    --label: #2a1a10;
    --card-white: #ffffff;
    --card-grey: #ededed;
    --brand-red: #e31e26;
    --brand-red-deep: #a81b22;
    --ink: #111111;
    --text-grey: #444444;
  }
  * { box-sizing: border-box; margin: 0; padding: 0; }
  html, body { width: 1200px; height: 788px; overflow: hidden; }
  body {
    position: relative;
    background: var(--backdrop);
    font-family: "Archivo", Arial, sans-serif;
  }
  .card-label {
    position: absolute;
    width: 524px;
    text-align: center;
    font-family: "Questrial", sans-serif;
    font-size: 21px;
    color: var(--label);
  }
  .card {
    position: absolute;
    width: 524px;
    height: 300px;
    border-radius: 22px;
    overflow: hidden;
    background: var(--card-white);
    box-shadow: 0 4px 10px rgba(0,0,0,0.35);
  }
  .col-left { left: 54px; }
  .col-right { left: 622px; }
  .row-top { top: 75px; }
  .row-bottom { top: 446px; }
  .label-top { top: 34px; }
  .label-bottom { top: 405px; }

  .accent-band {
    position: absolute;
    top: 0; right: 0; bottom: 0;
    width: 96px;
    background: linear-gradient(180deg, var(--brand-red) 0%, var(--brand-red) 55%, #7a1418 100%);
  }

  .brand {
    display: flex;
    align-items: center;
    gap: 10px;
  }
  .brand-name {
    font-family: "Archivo", sans-serif;
    font-weight: 900;
    font-size: 54px;
    letter-spacing: -1px;
    color: var(--ink);
    line-height: 1;
  }
  .brand-mark {
    width: 22px;
    height: 22px;
    background: var(--brand-red);
    align-self: flex-start;
  }

  .front .brand { position: absolute; left: 55px; top: 80px; }
  .front .brand-name { font-size: 46px; }
  .front .brand-mark { width: 19px; height: 19px; }
  .contact { position: absolute; left: 68px; top: 185px; }
  .contact-name {
    font-weight: 700;
    font-size: 17px;
    color: var(--brand-red);
    margin-bottom: 6px;
  }
  .contact-line {
    font-size: 13px;
    color: var(--text-grey);
    line-height: 21px;
  }
  .contact-line b { color: var(--ink); margin-right: 4px; }

  .back .brand {
    position: absolute;
    left: 0; right: 0; top: 95px;
    justify-content: center;
  }
  .site {
    position: absolute;
    left: 0; right: 0; top: 248px;
    text-align: center;
    font-family: "Questrial", sans-serif;
    font-size: 19px;
    color: var(--text-grey);
  }
  .back-red {
    background: linear-gradient(180deg, var(--brand-red-deep) 0%, #c42026 45%, #9c1a20 100%);
  }
  .back-red .brand-mark { background: var(--card-white); }
  .back-red .site { color: var(--card-white); }

  .back-grey { background: var(--card-grey); }
  .raised-panel {
    position: absolute;
    left: 80px; top: 80px;
    width: 362px; height: 130px;
    background: linear-gradient(180deg, #fafafa, #eeeeee);
    box-shadow: 0 8px 10px rgba(0,0,0,0.3);
    display: flex; align-items: center; justify-content: center;
  }
  .raised-panel .brand { position: static; }
  .raised-panel .brand-name { font-size: 40px; }
  .raised-panel .brand-mark { width: 16px; height: 16px; }
</style>
</head>
<body>
  <div class="card-label col-left label-top">Front</div>
  <div class="card-label col-right label-top">Back - 1</div>
  <div class="card-label col-left label-bottom">Back - 2</div>
  <div class="card-label col-right label-bottom">Back - 3</div>

  <section class="card front col-left row-top">
    <div class="accent-band" role="img" aria-label="Red and black curved swoosh decoration along the right edge"></div>
    <div class="brand">
      <span class="brand-name">LorvanTest</span>
      <span class="brand-mark"></span>
    </div>
    <div class="contact">
      <p class="contact-name">Todd Merrick</p>
      <p class="contact-line"><b>p :</b>877-514-9073 ext. 318</p>
      <p class="contact-line"><b>e :</b>Todd@lorvantest.com</p>
      <p class="contact-line"><b>w :</b>www.LorvanTest.com</p>
    </div>
  </section>

  <section class="card back col-right row-top">
    <div class="brand">
      <span class="brand-name">LorvanTest</span>
      <span class="brand-mark"></span>
    </div>
    <p class="site">www.LorvanTest.com</p>
  </section>

  <section class="card back back-red col-left row-bottom">
    <div class="brand">
      <span class="brand-name">LorvanTest</span>
      <span class="brand-mark"></span>
    </div>
    <p class="site">www.LorvanTest.com</p>
  </section>

  <section class="card back back-grey col-right row-bottom">
    <div class="raised-panel">
      <div class="brand">
        <span class="brand-name">LorvanTest</span>
        <span class="brand-mark"></span>
      </div>
    </div>
    <p class="site">www.LorvanTest.com</p>
  </section>
</body>
</html>
```